Blood Sugar WordPress Redesign

IMPORTANT: the design will need to look nice on mobile...so please keep that in mind!
We need to redesign our current Wordpress page to make it more appealing and look like an ecommerce page. We need the ability to implement this design on our Wordpress site.
Here is the current page: https://www.kplarewellness.com/supplements/vital-prime-daily/
However, the reference sample of what it has to look like or complement is also attached.
Attached is the Word document is the copy for the new page and the FAQs text.
The color palette for the page is attached also.
Thanks!

```html
<!DOCTYPE html>
<html lang="en">
<head>
<meta charset="utf-8">
<title>Vital Prime Daily – Product Page</title>
<link href="https://fonts.googleapis.com/css2?family=Outfit:wght@300;400;500;600;700;800&family=Tinos:wght@400;700&display=swap" rel="stylesheet">
<style>
:root{
  --stage:#8a8a8a;
  --blue:#4a55d2;
  --blue-deep:#2f36b8;
  --blue-soft:#7b8ff0;
  --navy:#1c2170;
  --tint:#eef2fc;
  --tint-2:#dfe6fa;
  --ink:#111;
  --text:#4a4a55;
  --white:#fff;
  --gold:#e5a21c;
  --photo:linear-gradient(160deg,#b89a86,#6e5446);
  --product:radial-gradient(circle at 40% 40%,#ffffff,#dfe3f3 60%,#b6bfe6);
}
*{box-sizing:border-box}
html,body{margin:0}
body{width:1058px;height:1200px;overflow:hidden;background:var(--stage);font-family:'Outfit',sans-serif;color:var(--ink);position:relative}
.page{position:absolute;top:57px;background:var(--white);display:flex;flex-direction:column}
.page--a{left:156px;width:221px;height:1085px}
.page--b{left:409px;width:232px;height:1032px}
.page--c{left:666px;width:235px;height:1030px}
.sec{position:relative;flex:none;overflow:hidden}
.sec--tint{background:var(--tint)}
.sec--blue{background:var(--blue);color:var(--white)}
.abs{position:absolute}
.h2{position:absolute;left:0;right:0;margin:0;text-align:center;font-size:9.6px;font-weight:600;line-height:1.18;letter-spacing:-.25px}
.h2 em{font-style:normal;color:var(--blue)}
.sec--blue .h2{color:var(--white)}
.rule{position:absolute;left:50%;width:26px;margin-left:-13px;height:1px;background:var(--blue)}
.rule::after{content:"";position:absolute;left:11px;top:-1px;width:3px;height:3px;border-radius:50%;background:var(--blue)}
.sec--blue .rule,.sec--blue .rule::after{background:var(--white)}
.p{margin:0;font-size:3px;line-height:1.45;color:var(--text)}
.sec--blue .p{color:#e6e9ff}
.list{margin:0;padding:0;list-style:none}
.list li{position:relative;padding-left:6px;margin-bottom:3px;font-size:3px;line-height:1.4;color:var(--text)}
.list li::before{content:"";position:absolute;left:0;top:1px;width:2.4px;height:2.4px;border-radius:50%;background:var(--blue)}
.sec--blue .list li{color:#e6e9ff}
.sec--blue .list li::before{background:var(--white)}
.list b{display:block;color:var(--blue);font-weight:600;font-size:3.6px}
.sec--blue .list b{color:var(--white)}
.btn{position:absolute;display:flex;align-items:center;justify-content:center;border-radius:8px;background:var(--blue);color:var(--white);font-size:3.6px;font-weight:600;letter-spacing:.2px;text-transform:uppercase}
.btn--navy{background:var(--navy)}
.circle-photo{position:absolute;border-radius:50%;background:var(--photo);box-shadow:0 0 0 3px #fff,0 0 0 7px #c9d0f4,0 0 0 9px #e5e9fb}
.thumb{position:absolute;border-radius:3px;background:var(--photo)}
.play{position:absolute;left:50%;top:50%;width:11px;height:11px;margin:-5.5px;border-radius:50%;border:1px solid #fff;background:rgba(255,255,255,.25)}
.play::after{content:"";position:absolute;left:4px;top:2.7px;border-left:3.6px solid #fff;border-top:2.3px solid transparent;border-bottom:2.3px solid transparent}
.arrows{position:absolute;display:flex;gap:3px}
.arrows span{width:12px;height:12px;border-radius:50%;border:1px solid #dde1f2;background:#fff;color:var(--blue);font-size:6px;display:flex;align-items:center;justify-content:center}
.arrows span+span{background:var(--blue);border-color:var(--blue);color:#fff}
.bottles{position:absolute;background:var(--product);border-radius:8px}
.logo{font-weight:700;font-size:7px;letter-spacing:.3px;color:var(--ink);display:flex;align-items:center;gap:2px}
.logo i{width:4px;height:4px;border-radius:50%;background:var(--blue);display:inline-block}
.benefit{position:absolute;margin:0;width:36px;text-align:center;font-size:3.3px;font-weight:500;line-height:1.25}
</style>
</head>
<body>

<main class="page page--a">

  <header class="sec" style="height:22px">
    <div class="logo abs" style="left:13px;top:7px"><i></i>KPLARE</div>
    <div class="abs" style="left:160px;top:5px;display:flex;gap:2px">
      <span style="background:#8f9af0;color:#fff;font-size:2.4px;padding:1px 4px;border-radius:4px">Wellness Shop</span>
      <span style="background:var(--blue);color:#fff;font-size:2.4px;padding:1px 5px;border-radius:4px">Login</span>
    </div>
    <nav class="abs" style="left:80px;top:13px;display:flex;gap:6px;font-size:2.2px;color:#555;align-items:center">
      <span style="background:#555;color:#fff;padding:1px 3px;border-radius:1px">HOME</span>
      <span>SUCCESS STORIES</span><span>MEDIA ROOM</span><span>ABOUT</span><span>BLOGS</span><span>CONTACT US</span>
    </nav>
  </header>

  <section class="sec sec--tint" style="height:157px">
    <div class="abs" style="left:110px;top:-10px;width:170px;height:170px;border-radius:50%;background:radial-gradient(circle,#c9d1f7 0,#dfe5fb 45%,rgba(238,242,252,0) 70%)"></div>
    <h1 class="abs" style="left:13px;top:22px;margin:0;line-height:.95">
      <span style="display:block;font-size:17px;font-weight:600;color:var(--blue);letter-spacing:-.3px">Vital Prime</span>
      <span style="display:block;font-size:27px;font-weight:700;letter-spacing:-.5px">Daily</span>
    </h1>
    <p class="abs" style="left:13px;top:72px;width:100px;margin:0;font-size:6px;line-height:1.35;color:#333">The Natural Way to Boost GLP-1 Levels to Support Fat Loss Control Hunger and Reduce Food Cravings</p>
    <div class="btn" style="left:13px;top:116px;width:52px;height:14px">Shop Now</div>
    <div class="bottles" role="img" aria-label="Three Vital Prime Daily supplement bottles" style="left:120px;top:40px;width:92px;height:82px"></div>
  </section>

  <section class="sec" style="height:198px">
    <h2 class="h2" style="top:15px">Struggling with stubborn weight gain,<br><em>energy crashes, or blood sugar spikes?</em></h2>
    <div class="rule" style="top:45px"></div>
    <p class="p abs" style="left:18px;right:18px;top:51px;text-align:center">Vital Prime Daily is here to help! This advanced formula helps stabilize blood sugar, control cravings, and support a healthier weight so you feel energized and in control all day.</p>
    <div class="circle-photo" role="img" aria-label="Smiling woman in a pink blazer holding the supplement bottle" style="left:14px;top:78px;width:83px;height:88px"></div>
    <p class="abs" style="left:108px;top:70px;width:105px;margin:0;font-size:4.4px;font-weight:600;line-height:1.2">Clinically-Studied Ingredients for Natural Weight Loss designed:</p>
    <ul class="list abs" style="left:108px;top:83px;width:102px">
      <li><b>Naturally increase GLP-1 levels</b>with clinically-tested ingredients so you eat less and stay full longer, reducing appetite</li>
      <li><b>Support fat loss, accelerate fat burning and reduce body weight,</b>including visceral belly fat, when combined with a healthy lifestyle</li>
      <li>By boosting GLP-1, your body sends signals to the brain that reduce cravings, quiet food noise and help you feel full longer naturally</li>
      <li><b>For anyone who wants fast, healthy weight loss</b>as well as for diabetics, pre-diabetics, and those with insulin resistance</li>
    </ul>
    <div class="btn" style="left:108px;top:167px;width:40px;height:11px">Shop Now</div>
  </section>

  <section class="sec sec--tint" style="height:207px">
    <h2 class="h2" style="top:18px">Why Your Blood Sugar <em>Balance Matters</em></h2>
    <ul class="list abs" style="left:13px;right:12px;top:44px"><li>Fluctuating blood sugar isn't just a problem for diabetics. It can affect weight gain, energy, cravings and long-term health. When blood sugar spikes, your body stores excess glucose as fat. If you notice any of the following, it may be time to focus on healthy blood sugar levels.</li></ul>
    <p class="abs" style="left:13px;top:64px;margin:0;font-size:4.4px;font-weight:600">Common Signs of Blood Sugar Imbalance:</p>
    <ul class="list abs" style="left:20px;top:75px;width:112px">
      <li><b>Frequent Energy Crashes</b>Do you feel exhausted after meals or struggle with afternoon fatigue? Sugar swings can leave you sluggish.</li>
      <li><b>Intense Sugar &amp; Carb Cravings</b>If you constantly crave sweets or processed carbs, your blood sugar may be swinging too high or too low.</li>
      <li><b>Difficulty Managing Weight</b>Struggling with stubborn weight gain around the midsection? Imbalances influence how your body stores fat.</li>
      <li><b>Feeling Hungry Soon After Eating</b>If you eat a meal but feel hungry again shortly after, your body isn't processing glucose well.</li>
      <li><b>Poor Sleep Quality</b>Blood sugar instability can disrupt sleep, making it harder to fall asleep or stay asleep.</li>
    </ul>
    <div class="circle-photo" role="img" aria-label="Vital Prime Daily bottle in a blue circle" style="left:128px;top:74px;width:80px;height:88px;background:radial-gradient(circle,#fff 0,#e7eafa 40%,#5561d8 75%)"></div>
    <div class="btn" style="left:20px;top:178px;width:40px;height:12px">Buy Now</div>
  </section>

  <section class="sec" style="height:151px">
    <h2 class="h2" style="top:18px">Real People, <em>Real Results</em></h2>
    <div class="rule" style="top:33px"></div>
    <div class="thumb" role="img" aria-label="Customer video testimonial" style="left:13px;top:43px;width:62px;height:70px"><span class="play"></span></div>
    <div class="thumb" role="img" aria-label="Customer video testimonial" style="left:80px;top:43px;width:62px;height:70px"><span class="play"></span></div>
    <div class="thumb" role="img" aria-label="Customer video testimonial" style="left:147px;top:43px;width:62px;height:70px"><span class="play"></span></div>
    <div class="arrows" style="left:96px;top:120px"><span>&larr;</span><span>&rarr;</span></div>
  </section>

  <section class="sec sec--tint" style="height:350px">
    <h2 class="h2" style="top:18px">Powerful Ingredients, <em>Backed by Science</em></h2>
    <div class="rule" style="top:33px"></div>
    <p class="abs" style="left:13px;top:43px;margin:0;font-size:4.4px;font-weight:600">The Power of Citrovia®</p>
    <p class="p abs" style="left:13px;right:12px;top:51px">Citrovia® is a patented citrus flavonoid blend clinically studied for its impact on blood sugar regulation, insulin function and overall metabolic health. Research suggests it supports glucose metabolism by:</p>
    <div class="circle-photo" role="img" aria-label="Smiling woman holding the supplement bottle" style="left:17px;top:66px;width:80px;height:90px"></div>
    <ul class="list abs" style="left:102px;top:70px;width:110px">
      <li><b>Boosting GLP-1 Levels</b>Shown to increase GLP-1, a hormone that plays a crucial role in blood sugar and appetite control.</li>
      <li><b>Reducing Fasting Blood Sugar</b>Clinical studies indicate it helps keep blood glucose within a healthy range, a promising natural option.</li>
      <li><b>Enhancing Insulin Sensitivity</b>By promoting normal insulin function, it may support efficient glucose uptake and steady energy.</li>
      <li><b>Lowering Inflammation</b>High blood sugar levels add to oxidative stress; research suggests it helps combat these effects.</li>
    </ul>
    <p class="p abs" style="left:13px;right:12px;top:166px;font-style:italic;font-size:2.7px"><span style="color:var(--blue)">Reference:</span> Almeida, C., Duarte, T., &amp; Reis, G. (2019). Effectiveness of Citrovia® in managing hyperglycemia and reversal of prediabetes condition: A double-blind, randomized, controlled study. Botanical Health Research, 33(7), 1921–1930</p>
    <svg class="abs" style="left:39px;top:184px" width="142" height="153" viewBox="0 0 242 260" role="img" aria-label="Bar chart: Citrovia increases GLP-1 levels in clinical study">
      <rect x="0" y="0" width="242" height="260" rx="14" fill="#c9d6ee"/>
      <rect x="0" y="225" width="242" height="35" fill="#e4eaf7"/>
      <rect x="17" y="22" width="209" height="50" rx="25" fill="#fff" stroke="#1c2170" stroke-width="1.5"/>
      <text x="121" y="43" text-anchor="middle" font-family="Tinos,serif" font-size="13" fill="#111">Citrovia® Increases GLP-1 Levels</text>
      <text x="121" y="60" text-anchor="middle" font-family="Tinos,serif" font-size="13" fill="#111">in Clinical Study</text>
      <rect x="62" y="86" width="7" height="7" fill="#7f9ae0"/><text x="73" y="92" font-size="5" fill="#333" font-family="Outfit,sans-serif">Placebo</text>
      <rect x="128" y="86" width="7" height="7" fill="#1c2170"/><text x="139" y="92" font-size="5" fill="#333" font-family="Outfit,sans-serif">Citrovia® 200 mg</text>
      <rect x="50" y="106" width="180" height="120" fill="#fff" opacity=".6"/>
      <g stroke="#9aa7c8" stroke-width=".6"><line x1="50" y1="112" x2="230" y2="112"/><line x1="50" y1="148" x2="230" y2="148"/><line x1="50" y1="183" x2="230" y2="183" stroke="#333" stroke-width="1"/><line x1="50" y1="219" x2="230" y2="219"/><line x1="50" y1="106" x2="50" y2="226" stroke="#333"/></g>
      <g font-size="5" fill="#333" font-family="Outfit,sans-serif" text-anchor="end"><text x="45" y="114">20%</text><text x="45" y="150">10%</text><text x="45" y="185">0%</text><text x="45" y="221">-10%</text></g>
      <rect x="53" y="176" width="27" height="7" fill="#7f9ae0"/>
      <rect x="80" y="122" width="27" height="61" fill="#1c2170"/>
      <rect x="148" y="183" width="27" height="18" fill="#7f9ae0"/>
      <rect x="175" y="105" width="27" height="78" fill="#1c2170"/>
      <g fill="#fff"><path d="M93 132l2 5 5 2-5 2-2 5-2-5-5-2 5-2z"/><path d="M188 115l2 5 5 2-5 2-2 5-2-5-5-2 5-2z"/></g>
      <g font-size="5" fill="#333" font-family="Outfit,sans-serif" text-anchor="middle"><text x="66" y="192">+0.2%</text><text x="94" y="192">17%</text><text x="161" y="209">-5%</text><text x="189" y="192">22%</text></g>
      <g font-size="5.5" font-weight="600" fill="#111" font-family="Outfit,sans-serif" text-anchor="middle"><text x="80" y="238">STUDY 1</text><text x="175" y="238">STUDY 2</text></g>
      <text x="121" y="251" text-anchor="middle" font-size="3" fill="#555" font-family="Outfit,sans-serif">Source: results showed lower glucose and a 22% GLP-1 rise versus placebo at 12 weeks.</text>
    </svg>
  </section>
</main>

<main class="page page--b">

  <section class="sec" style="height:191px">
    <h2 class="h2" style="top:14px">Other Key Ingredients for<br><em>Comprehensive Blood Sugar Support</em></h2>
    <div class="rule" style="top:42px"></div>
    <ul class="list abs" style="left:13px;top:62px;width:120px">
      <li><b>Cinnamon Bark – Nature's Blood Sugar Balancer</b>Widely studied for its ability to help regulate blood sugar. It improves insulin sensitivity, helps the body use glucose efficiently and reduces post-meal spikes.</li>
      <li><b>Chromium Picolinate – Essential for Insulin Function</b>A vital trace mineral with a key role in carbohydrate and lipid metabolism. It enhances insulin effectiveness, helps cells absorb glucose and may curb sugar cravings.</li>
      <li><b>Alpha-Lipoic Acid – A Potent Antioxidant for Glucose Metabolism</b>A powerful antioxidant that helps move glucose into cells, reduces sugar levels and fights oxidative stress linked to metabolic imbalance.</li>
    </ul>
    <div class="circle-photo" role="img" aria-label="Open supplement bottle with capsules" style="left:140px;top:52px;width:78px;height:88px;background:radial-gradient(circle,#fff 0,#e7eafa 45%,#6a74dc 80%);box-shadow:none"></div>
    <p class="p abs" style="left:13px;right:12px;top:167px">Together, these ingredients create a well-rounded formula to promote stable blood sugar levels, support fat loss and help control cravings, empowering you to take control of your health.</p>
  </section>

  <section class="sec sec--blue" style="height:186px">
    <h2 class="h2" style="top:18px">Who Is Vital Prime Daily For?</h2>
    <div class="circle-photo" role="img" aria-label="Smiling woman holding the supplement bottle" style="left:12px;top:40px;width:86px;height:100px;box-shadow:0 0 0 3px #6b76e0,0 0 0 6px #5a65d9"></div>
    <p class="p abs" style="left:108px;top:46px;width:112px">Whether you are managing specific health concerns or striving for overall wellness, this formula provides targeted support.</p>
    <ul class="list abs" style="left:108px;top:61px;width:112px">
      <li><b>Individuals Seeking Healthy Weight Management</b>Balanced blood sugar plays a role in metabolism and fat storage, helping maintain normal glucose levels as part of a balanced lifestyle.</li>
      <li><b>Those Looking to Support Blood Sugar Balance</b>Fluctuations in blood sugar can impact energy, cravings and well-being. Its ingredients support healthy glucose metabolism and insulin function.</li>
      <li><b>Anyone Looking for Sustained Energy &amp; Fewer Cravings</b>A balanced blood sugar response can help prevent energy crashes and sugar cravings throughout the day.</li>
    </ul>
    <ul class="list abs" style="left:13px;right:12px;top:153px">
      <li><b>Individuals with Dietary &amp; Lifestyle Concerns</b>If you are mindful of carbohydrate intake, energy levels or sugar cravings, this formula provides nutritional support to complement a healthy diet and active lifestyle.</li>
    </ul>
  </section>

  <section class="sec" style="height:259px">
    <h2 class="h2" style="top:19px">Why Customers Love <em>Vital Prime Daily</em></h2>
    <div class="thumb" role="img" aria-label="Customer video review" style="left:13px;top:51px;width:65px;height:73px"><span class="play"></span></div>
    <div class="thumb" role="img" aria-label="Customer video review" style="left:84px;top:51px;width:65px;height:73px"><span class="play"></span></div>
    <div class="thumb" role="img" aria-label="Customer video review" style="left:154px;top:51px;width:65px;height:73px"><span class="play"></span></div>
    <div class="arrows" style="left:101px;top:135px"><span>&larr;</span><span>&rarr;</span></div>
    <div class="abs" role="img" aria-label="Decorative wavy connector linking five benefit icons" style="left:13px;top:160px;width:206px;height:90px;border-radius:8px;background:linear-gradient(90deg,#f2f5fd,#e3e9fb 50%,#f2f5fd)"></div>
    <p class="benefit" style="left:20px;top:223px">Naturally Boost GLP-1 Levels*</p>
    <p class="benefit" style="left:58px;top:186px">Naturally Feel Full Faster &amp; Stay Full Longer*</p>
    <p class="benefit" style="left:96px;top:203px">Reduce Food Cravings and Overall Appetite*</p>
    <p class="benefit" style="left:134px;top:189px">Maximize Fat Burning in the Body*</p>
    <p class="benefit" style="left:172px;top:205px">Manage Blood Sugar Levels*</p>
  </section>

  <section class="sec sec--tint" style="height:194px">
    <h2 class="h2" style="top:18px">Take Control of Your<br><em>Blood Sugar &amp; Metabolism Today!</em></h2>
    <p class="p abs" style="left:13px;top:55px;width:120px">Don't let unstable blood sugar hold you back. Whether you're looking to support fat loss, curb cravings, support healthy blood sugar or boost your metabolism, Vital Prime Daily is here to help.</p>
    <ul class="list abs" style="left:13px;top:80px;width:112px">
      <li style="font-size:4px;color:#111;font-weight:500">Promote healthy weight loss and support fat loss</li>
      <li style="font-size:4px;color:#111;font-weight:500">Support normal insulin function</li>
      <li style="font-size:4px;color:#111;font-weight:500">Manage sugar cravings &amp; energy crashes</li>
    </ul>
    <p class="abs" style="left:13px;top:113px;margin:0;font-size:10px;font-weight:600;color:var(--blue)">Ready to feel your best?</p>
    <p class="abs" style="left:13px;top:129px;width:115px;margin:0;font-size:6.5px;line-height:1.3">Try Vital Prime Daily today and experience the difference!</p>
    <div class="btn" style="left:13px;top:154px;width:54px;height:15px">Order Now</div>
    <div class="circle-photo" role="img" aria-label="Woman in glasses holding the supplement bottle" style="left:131px;top:60px;width:90px;height:96px"></div>
  </section>

  <section class="sec" style="height:203px">
    <h2 class="h2" style="top:16px">Our Customers are <em>Loving Their Results</em></h2>
    <div class="rule" style="top:33px"></div>
    <div class="thumb" role="img" aria-label="Customer before and after weight loss photos" style="left:13px;top:46px;width:98px;height:80px"></div>
    <div class="thumb" role="img" aria-label="Customer before and after weight loss photos" style="left:120px;top:46px;width:99px;height:80px"></div>
    <div class="abs" style="left:13px;top:118px;width:98px;height:8px;display:flex;font-size:3.6px;color:#fff">
      <span style="flex:1;background:var(--blue);display:flex;align-items:center;justify-content:center">Before</span>
      <span style="flex:1;background:var(--blue-deep);display:flex;align-items:center;justify-content:center;margin-left:1px">After</span>
    </div>
    <div class="abs" style="left:120px;top:118px;width:99px;height:8px;display:flex;font-size:3.6px;color:#fff">
      <span style="flex:1;background:var(--blue);display:flex;align-items:center;justify-content:center">Before</span>
      <span style="flex:1;background:var(--blue-deep);display:flex;align-items:center;justify-content:center;margin-left:1px">After</span>
    </div>
    <p class="p abs" style="left:13px;top:132px;width:98px">Marisa Lost 166 Pounds and Looks AMAZING! She says: "I do low carb and focus mainly on lean meats and veggies while continuing to do the green smoothie cleanse. I use Liver Prime and Vital Prime Daily regularly. I don't have sugar cravings anymore, especially for ice cream. I now work out 4 days per week."</p>
    <p class="p abs" style="left:120px;top:132px;width:99px">Janelle says: "I'm back at my desired weight. That's due to combining Liver Prime and Vital Prime Daily. Everything else I did is what I've done for years. I used cleanses and yoga, but it wasn't until I added Vital Prime Daily that I saw REAL progress in the stomach and waist area. This is the REAL DEAL y'all!"</p>
    <div class="arrows" style="left:101px;top:186px"><span>&larr;</span><span>&rarr;</span></div>
  </section>
</main>

<main class="page page--c">

  <section class="sec sec--tint" style="height:294px">
    <h2 class="h2" style="top:17px">What to Expect<br><em>When Taking Vital Prime Daily</em></h2>
    <div class="rule" style="top:47px"></div>
    <p class="abs" style="left:0;right:0;top:60px;margin:0;text-align:center;font-size:5px;font-weight:500">Here's what you can expect over <span style="color:var(--blue);font-size:6.5px;font-weight:600">three months</span> of regular use:</p>

    <div class="abs" style="left:38px;top:89px;width:159px;height:48px;border-radius:4px;background:var(--blue-soft);color:#fff;text-align:center">
      <p style="margin:19px 0 0;font-size:5px;font-weight:500">Reduced Hunger and Cravings for Carbs and Sugar</p>
      <p style="margin:6px 14px 0;font-size:3.4px;line-height:1.35;color:#eef">Participants in a clinical study showed decreased hunger and reduced sugar cravings after 4-8 weeks*</p>
    </div>
    <div class="abs" style="left:38px;top:154px;width:159px;height:48px;border-radius:4px;background:var(--blue);color:#fff;text-align:center">
      <p style="margin:19px 0 0;font-size:5px;font-weight:500">Healthy Fat Loss and Reduction in Body Weight</p>
      <p style="margin:6px 10px 0;font-size:3.4px;line-height:1.35;color:#eef">Participants in a clinical study showed a reduction in body weight, visceral fat and hip and waist circumference, with a healthy lifestyle*</p>
    </div>
    <div class="abs" style="left:38px;top:219px;width:159px;height:52px;border-radius:4px;background:var(--blue-deep);color:#fff;text-align:center">
      <p style="margin:19px 0 0;font-size:5px;font-weight:500">Increased GLP-1 Levels and Healthy Blood Sugar Levels</p>
      <p style="margin:6px 10px 0;font-size:3.4px;line-height:1.35;color:#eef">Participants in a 12-week clinical study using a citrus bioflavonoid complex showed higher GLP-1 levels and blood sugar within the normal range*</p>
    </div>
    <div class="abs" style="left:104px;top:75px;width:27px;height:27px;border-radius:50%;background:var(--blue-soft);border:1.5px solid #fff;color:#fff;font-size:4px;line-height:1.15;text-align:center;padding-top:5px">After<br>Month<br>1</div>
    <div class="abs" style="left:104px;top:140px;width:27px;height:27px;border-radius:50%;background:var(--blue);border:1.5px solid #fff;color:#fff;font-size:4px;line-height:1.15;text-align:center;padding-top:5px">After<br>Month<br>2</div>
    <div class="abs" style="left:104px;top:205px;width:27px;height:27px;border-radius:50%;background:var(--blue-deep);border:1.5px solid #fff;color:#fff;font-size:4px;line-height:1.15;text-align:center;padding-top:5px">After<br>Month<br>3</div>
  </section>

  <section class="sec" style="height:207px">
    <h2 class="h2" style="top:15px">Want Faster Weight Loss?<br><em>Try the Complete Weight Loss Bundle!</em></h2>
    <div class="bottles" role="img" aria-label="Three bundle supplement bottles on a soft pink and blue glow" style="left:12px;top:60px;width:88px;height:76px;background:radial-gradient(circle,#fff 0,#f3e6f3 50%,#e6ebfb 80%)"></div>
    <ul class="list abs" style="left:97px;top:53px;width:127px"><li>While Vital Prime Daily provides powerful support for blood sugar balance, combining it with our full Weight Loss Bundle takes your results to the next level.</li></ul>
    <p class="abs" style="left:118px;top:73px;margin:0;font-size:3.8px;font-weight:600">The Weight Loss Bundle includes:</p>
    <ul class="list abs" style="left:118px;top:80px;width:95px">
      <li style="margin-bottom:2px"><b style="color:#c43db0">Liver Prime</b>A liver detox that accelerates fat burning in the body and supports liver health</li>
      <li style="margin-bottom:2px"><b style="color:#d22a3a">Tummy Prime</b>Improves digestion, promotes regularity, reduces bloating and supports gut health</li>
      <li><b>Vital Prime Daily</b>Supports fat loss, reduces cravings and stabilizes blood sugar</li>
    </ul>
    <ul class="list abs" style="left:97px;top:144px;width:127px">
      <li><span style="color:#111;font-weight:600">Why bundle?</span> These three products work synergistically to reset your metabolism, eliminate waste and keep your body in fat-burning mode.</li>
      <li><span style="color:#111;font-weight:600">Bundle &amp; Save!</span> Get all three at a discounted price for the ultimate full-body weight management support.</li>
    </ul>
    <div class="btn" style="left:44px;top:179px;width:147px;height:12px;background:var(--blue-deep)">Upgrade to the Weight Loss Bundle &amp; Save Now!</div>
  </section>

  <section class="sec sec--tint" style="height:167px">
    <h2 class="h2" style="top:16px">Frequently Asked <em>Questions</em></h2>
    <div class="abs" style="left:13px;top:46px;width:103px;font-size:2.5px;color:#333">
      <div style="background:#fff;height:7px;margin-bottom:3px;display:flex;align-items:center;justify-content:space-between;padding:0 2px"><span><b style="color:var(--blue)">01</b> What are the benefits of Vital Prime Daily?</span><span style="color:var(--blue)">⊕</span></div>
      <div style="background:var(--blue);color:#fff;height:7px;display:flex;align-items:center;justify-content:space-between;padding:0 2px"><span><b>02</b> Can Vital Prime Daily help with belly fat?</span><span>⊖</span></div>
      <div style="background:#fff;padding:2px 3px;margin-bottom:3px;line-height:1.35;font-size:2.2px">Yes, it balances key hormones, namely insulin, that cause stubborn belly fat. By lowering insulin levels, it helps target visceral fat around the waistline that is driven by these hormones.</div>
      <div style="background:#fff;height:7px;margin-bottom:3px;display:flex;align-items:center;justify-content:space-between;padding:0 2px"><span><b style="color:var(--blue)">03</b> Can it be taken with Liver Prime?</span><span style="color:var(--blue)">⊕</span></div>
      <div style="background:#fff;height:7px;margin-bottom:3px;display:flex;align-items:center;justify-content:space-between;padding:0 2px"><span><b style="color:var(--blue)">04</b> How many do you take daily?</span><span style="color:var(--blue)">⊕</span></div>
      <div style="background:#fff;height:9px;margin-bottom:3px;display:flex;align-items:center;justify-content:space-between;padding:0 2px"><span><b style="color:var(--blue)">05</b> It features Citrovia®, what is this ingredient?</span><span style="color:var(--blue)">⊕</span></div>
      <div style="background:#fff;height:7px;margin-bottom:3px;display:flex;align-items:center;justify-content:space-between;padding:0 2px"><span><b style="color:var(--blue)">06</b> Who is Vital Prime Daily for?</span><span style="color:var(--blue)">⊕</span></div>
      <div style="background:#fff;height:7px;display:flex;align-items:center;justify-content:space-between;padding:0 2px"><span><b style="color:var(--blue)">07</b> What are the ingredients?</span><span style="color:var(--blue)">⊕</span></div>
    </div>
    <div class="circle-photo" role="img" aria-label="Smiling woman with braids holding the supplement bottle" style="left:125px;top:34px;width:96px;height:108px"></div>
  </section>

  <section class="sec sec--blue" style="height:178px;overflow:visible;z-index:2">
    <h2 class="h2" style="top:14px">Still Unsure if<br>Vital Prime Daily is Right for You?</h2>
    <div class="rule" style="top:42px"></div>
    <div class="circle-photo" role="img" aria-label="Woman in a white top holding the supplement bottle" style="left:14px;top:47px;width:89px;height:96px;box-shadow:0 0 0 3px #6b76e0,0 0 0 6px #5a65d9"></div>
    <p class="p abs" style="left:123px;top:58px;width:98px">We understand choosing the right supplement is a big decision. If you're still on the fence, why not give Vital Prime Daily a try with confidence?</p>
    <p class="abs" style="left:123px;top:79px;margin:0;font-size:6px;line-height:1.3">Here's the best part<br><i>Subscribe today and get</i></p>
    <p class="abs" style="left:123px;top:101px;margin:0;font-size:8px;font-weight:600">10% OFF <span style="font-size:5.5px">your first order!</span></p>
    <p class="p abs" style="left:123px;top:116px;width:92px">Take the first step toward balanced blood sugar, stable energy and effortless weight loss</p>
    <div class="btn btn--navy" style="left:123px;top:135px;width:47px;height:12px">Order Now</div>
    <div class="abs" role="img" aria-label="60-day money back guarantee seal" style="left:167px;top:137px;width:56px;height:54px;border-radius:50%;background:radial-gradient(circle,#f2c14a 0,#e5a21c 60%,#b87c0c 100%);box-shadow:0 0 0 2px #f6d27a"></div>
  </section>

  <section class="sec" style="height:113px">
    <h2 class="h2" style="top:26px">Customer <em>Reviews</em></h2>
    <div class="rule" style="top:41px"></div>
    <p class="abs" style="left:0;right:0;top:60px;margin:0;text-align:center;font-size:11.5px;font-weight:300;line-height:1.2;color:#e7e7ec">SPACE FOR<br>REVULY REVIEWS</p>
  </section>

  <footer class="sec sec--tint" style="height:71px">
    <div class="logo abs" style="left:0;right:0;top:13px;justify-content:center"><i></i>KPLARE</div>
    <div class="abs" style="left:40px;top:28px;display:flex;gap:8px;font-size:2.3px;color:#444;line-height:1.3">
      <span style="display:flex;gap:2px"><svg width="5" height="5" viewBox="0 0 10 10"><rect width="10" height="10" rx="2" fill="#4a55d2"/><path d="M3 2c-1 1 0 4 2 5s3 1 3 0l-1-1-1 1-2-2 1-1-1-1z" fill="#fff"/></svg><span>CALL US<br>(555) 014-2290</span></span>
      <span style="display:flex;gap:2px"><svg width="5" height="5" viewBox="0 0 10 10"><rect width="10" height="10" rx="2" fill="#4a55d2"/><path d="M2 3h6v4H2zM2 3l3 2 3-2" fill="none" stroke="#fff"/></svg><span>EMAIL US<br>hello@kplarewellness.com</span></span>
      <span style="display:flex;gap:2px"><svg width="5" height="5" viewBox="0 0 10 10"><rect width="10" height="10" rx="2" fill="#4a55d2"/><path d="M5 8S3 5.5 3 4a2 2 0 0 1 4 0c0 1.5-2 4-2 4z" fill="#fff"/></svg><span>Brightway Publishing 480 Harbor Lane Suite 12<br>Fairview, MD 20900</span></span>
    </div>
    <div class="abs" style="left:13px;right:13px;top:43px;height:.5px;background:#cfd4e6"></div>
    <nav class="abs" style="left:0;right:0;top:51px;display:flex;justify-content:center;gap:9px;font-size:2.3px;color:#444">
      <span>HOME</span><span>SUCCESS STORIES</span><span>MEDIA ROOM</span><span>ABOUT</span><span>BLOGS</span><span>CONTACT US</span>
    </nav>
    <div class="abs" style="left:0;right:0;top:61px;height:10px;background:var(--blue);display:flex;align-items:center;justify-content:space-between;padding:0 13px">
      <span style="font-size:2px;color:#dfe3ff">Copyright © 2025 All Rights Reserved by KPLARE</span>
      <span style="display:flex;gap:1.5px"><i style="width:4px;height:4px;border:.5px solid #fff;border-radius:1px"></i><i style="width:4px;height:4px;border:.5px solid #fff;border-radius:1px"></i><i style="width:4px;height:4px;border:.5px solid #fff;border-radius:1px"></i><i style="width:4px;height:4px;border:.5px solid #fff;border-radius:1px"></i></span>
    </div>
  </footer>
</main>

</body>
</html>
```